TL - business card

Tallow Partners is an insurance brokerage firm, inovative, proactive, vigorous, which aims to become the leader of the insurance brokers in Anfrica. We should like to get some designs which should be avoided also in Gray / Metallic for the Administration and Orange / Blue for the Managers (ike in the picture sent). The Blue / Green logo is not the correct one, but the source of the file. Please adjust the color accordingly for the business cards. 1 / Orange / Blue 2 / Gray / Metallic We want something classic but which is transmitted strenght, inovation, modernity and most of all, rapidity. We want something start-up like, very punchy and catching eye remaining profesional at the same time. Name: Dorian Whitlock Function: Managing Director Address: N ° 17/18 Rua Veloso - R / C 2B Direita - Bairro Mutamba - Luanda Tel: (+244) 947 582 316 Email: dorian.whitlock@tallow-p.example Website: www.tallow-p. example We want classic in the front and creative, colorfull at the back. The cards will be printed in relief, with very high quality of paper.
Insurance Broker
Colors
Designer to choose colors to be used in the design.

```html
<!DOCTYPE html>
<html lang="en">
<head>
<meta charset="utf-8">
<title>Tallow Partners – Business Card</title>
<link href="https://fonts.googleapis.com/css2?family=Montserrat:wght@600;700&family=Lato:wght@400&display=swap" rel="stylesheet">
<style>
  :root {
    --stage: #2b2e33;
    --card-white: #ffffff;
    --brand-orange: #f5a11c;
    --brand-blue: #1f9ad6;
    --blue-deep: #1b8fd8;
    --blue-light: #2ab3e6;
    --text-grey: #5b5b5b;
    --rule-grey: #9a9a9a;
  }
  * { box-sizing: border-box; margin: 0; padding: 0; }
  html, body { width: 1200px; height: 900px; overflow: hidden; }
  body {
    background: var(--stage);
    display: flex;
    align-items: center;
    justify-content: center;
    gap: 100px;
    font-family: "Lato", Arial, sans-serif;
  }
  .card {
    width: 390px;
    height: 620px;
    border-radius: 34px;
    position: relative;
    overflow: hidden;
  }

  /* Back side */
  .card-back {
    background: linear-gradient(160deg, var(--blue-deep) 0%, var(--blue-light) 55%, var(--blue-deep) 100%);
  }
  .back-texture {
    position: absolute;
    inset: 0;
    background: linear-gradient(200deg, rgba(255,255,255,0.08), rgba(255,255,255,0) 70%);
  }
  .back-brand {
    position: absolute;
    left: 0; right: 0;
    bottom: 90px;
    display: flex;
    flex-direction: column;
    align-items: center;
    gap: 22px;
  }
  .back-dot {
    width: 44px; height: 44px;
    border: 3px solid #fff;
    border-radius: 50%;
  }
  .back-name {
    font-family: "Montserrat", Arial, sans-serif;
    font-weight: 700;
    font-size: 27px;
    letter-spacing: 1px;
    color: #fff;
    text-transform: uppercase;
  }

  /* Front side */
  .card-front {
    background: var(--card-white);
    display: flex;
    flex-direction: column;
    align-items: center;
    text-align: center;
    padding-top: 70px;
  }
  .front-mark {
    width: 70px; height: 70px;
    border-radius: 50%;
    border: 5px solid var(--brand-orange);
    margin-bottom: 16px;
  }
  .front-company {
    font-family: "Montserrat", Arial, sans-serif;
    font-weight: 700;
    font-size: 26px;
    letter-spacing: 0.5px;
    color: var(--brand-orange);
    text-transform: uppercase;
  }
  .person-name {
    margin-top: 58px;
    font-family: "Montserrat", Arial, sans-serif;
    font-weight: 700;
    font-size: 25px;
    color: var(--brand-orange);
    text-transform: uppercase;
  }
  .person-role {
    margin-top: 4px;
    font-size: 15px;
    color: var(--text-grey);
  }
  .rule {
    width: 230px;
    height: 1px;
    background: var(--rule-grey);
    margin: 12px 0;
  }
  .icons {
    display: flex;
    gap: 6px;
    margin-bottom: 10px;
  }
  .icons svg { width: 26px; height: 26px; }
  .contacts, .address {
    font-size: 15.5px;
    line-height: 1.45;
    color: var(--text-grey);
    letter-spacing: 0.3px;
  }
  .address { margin-top: 2px; }
</style>
</head>
<body>

  <section class="card card-back">
    <div class="back-texture" role="img" aria-label="Faint repeating pattern of small brand marks across the blue background"></div>
    <div class="back-brand">
      <div class="back-dot"></div>
      <div class="back-name">Tallow-Partners</div>
    </div>
  </section>

  <section class="card card-front">
    <div class="front-mark"></div>
    <div class="front-company">Tallow-Partners</div>

    <div class="person-name">Dorian Whitlock</div>
    <div class="person-role">Managing Director</div>
    <div class="rule"></div>

    <div class="icons">
      <svg viewBox="0 0 26 26" aria-label="Phone">
        <circle cx="13" cy="13" r="13" fill="var(--brand-blue)"/>
        <path d="M8 9c0-1 1-2 2-2l1.5 2.5-1 1.2c.8 1.7 2 2.9 3.6 3.7l1.2-1L18 15c0 1-1 2-2 2-4.5 0-8-3.5-8-8z" fill="#fff"/>
      </svg>
      <svg viewBox="0 0 26 26" aria-label="Email">
        <circle cx="13" cy="13" r="13" fill="var(--brand-blue)"/>
        <rect x="7" y="9" width="12" height="8.5" rx="1" fill="#fff"/>
        <path d="M7.5 9.5 13 14l5.5-4.5" fill="none" stroke="var(--brand-blue)" stroke-width="1.2"/>
      </svg>
      <svg viewBox="0 0 26 26" aria-label="Website">
        <circle cx="13" cy="13" r="13" fill="var(--brand-blue)"/>
        <g fill="none" stroke="#fff" stroke-width="1.2">
          <circle cx="13" cy="13" r="6"/>
          <ellipse cx="13" cy="13" rx="2.6" ry="6"/>
          <path d="M7 13h12M8 10h10M8 16h10"/>
        </g>
      </svg>
    </div>

    <div class="contacts">
      (+244) 947 582 316<br>
      dorian.whitlock@tallow-p.example<br>
      www.tallow-p.example
    </div>
    <div class="rule"></div>
    <div class="address">
      N ° 17/18 Rua Veloso - R / C 2B Direita<br>
      Bairro Mutamba - Luanda
    </div>
  </section>

</body>
</html>
```